Announcement for a New Trauma Therapy Group - Rack Card

I need a two-sided "rack" card that is 4x9 announcing a Women's Trauma and Loss Group. I am a licensed therapist and will be starting this support group for women who have experienced trauma of all kinds. In addition to groups, I offer individual, couples, and family counseling sessions.

I would like to see designs that are soft tones and use colors like muted blues, greens, and sand tones. The final design should communicate hope and healing as well as have a peaceful feel to it.

I would like a picture of a woman's profile from either the side or from behind her. (possibly a contemplative picture on a beach)

I am attaching a picture of myself to go alongside the bio information as well.

On One Side, I need the description of the group and contact info:

Mending the Weary Spirit
Women's Trauma & Loss Group
Led by Licensed Professional Counselor, Lena Marsh Pruitt

10 Week Group
Cost - $35 session
Group size limited to 10 participants

Topics Include:
What is Trauma?
How Trauma Affects Us
Creating a Feeling of Safety
Managing Trauma Triggers
Importance of Self Care
Healthy vs. Unhealthy Coping
Guilt, Shame, and Blame
Victim vs. Victimized
Grieving through Loss
Anger and Forgiveness
Imagining a Better Future

For More Information, Contact:
Lena Marsh Pruitt, LPC, LMFT
(555) 318-4926
lena@calmwatersguide.example

On Side Two:

Life hurts and does not seem fair. So what do you do when you are faced with an event in your life that knocks you off your feet? It seems no one understands what you are feeling and no one knows just what to say. It is tempting to pull away and isolate or put up a mask and pretend everything is OK.

It is my desire you know that you are not alone! There are others who understand the feelings you are going through and offer a safe place for encouraging support. I want to invite you to embark on a courageous journey of healing where you will not only learn how to "survive" after trauma and loss, but instead, learn that you can once again "thrive"!
- Lena Marsh Pruitt, LPC, LMFT

Lena Marsh Pruitt is a Licensed Professional Counselor and Licensed Marriage and Family Therapist. She is the owner of Quiet Harbor Counseling Services located in Tulsa, OK.

Lena is a trauma survivor herself and understands firsthand the unique challenges that can arise on the journey to healing.

(Include Lena's picture next to bio)

(Attach logo and business information to this side as well.)

Target Market(s)

Women who have gone through a traumatic experience or loss and are hurting emotionally

Industry/Entity Type

Counsellor

Font styles to use
Serif
Script

Colors
fbe7d2
86cfc6
cfeae6
85abd2
cfdeed

Requirements
Must have
• Lena's picture as well as her logo and contact information must be on the card.
• One side of the card should describe the group with the following description:
• "Mending the Weary Spirit"
• Women's Trauma & Loss Group
• Led by Licensed Professional Counselor, Lena Marsh Pruitt
• 10 Week Group
• Cost - $35 session
• Group size limited to 10 participants
• Topics Include:
• What is Trauma?
• How Trauma Affects Us
• Creating a Feeling of Safety
• Managing Trauma Triggers
• Importance of Self Care
• Healthy vs. Unhealthy Coping
• Guilt, Shame, and Blame
• Victim vs. Victimized
• Grieving through Loss
• Anger and Forgiveness
• Imagining a Better Future
• For More Information, Contact:
• Lena Marsh Pruitt, LPC, LMFT
• (555) 318-4926
• lena@calmwatersguide.example
• On the second side, it must have this note from Lena:
• Life hurts and does not seem fair. So what do you do when you are faced with an event in your life that knocks you off your feet? It seems no one understands what you are feeling and no one knows just what to say. It is tempting to pull away and isolate or put up a mask and pretend everything is OK.
• It is my desire you know that you are not alone! There are others who understand the feelings you are going through and offer a safe place for encouraging support. I want to invite you to embark on a courageous journey of healing where you will not only learn how to "survive" after trauma and loss, but instead, learn that you can once again "thrive"!
• - Lena Marsh Pruitt, LPC, LMFT
• Lena Marsh Pruitt is a Licensed Professional Counselor and Licensed Marriage and Family Therapist. She is the owner of Quiet Harbor Counseling Services located in Tulsa, OK.
• Lena is a trauma survivor herself and understands firsthand the unique challenges that can arise on the journey to healing. In addition to facilitating groups, Lena also offers individual, marriage, and family counseling.
Nice to have
• soft muted colors that are peaceful. Light blues, greens, sand colors would work well. A picture at the top of the card of either a woman or a woman's profile that is hopeful such as a woman sitting at a beach overlooking the ocean.
Should not have
• No harsh or bright bold colors. This card needs to have a peaceful feeling to it.

```html
<!DOCTYPE html>
<html lang="en">
<head>
<meta charset="utf-8">
<title>Women's Trauma &amp; Loss Group – Rack Card</title>
<link href="https://fonts.googleapis.com/css2?family=Lato:ital,wght@0,400;0,700;1,700&family=Pinyon+Script&display=swap" rel="stylesheet">
<style>
  :root{
    --green:#4c8a3c;
    --green-text:#3f7d30;
    --green-dark:#1f3a1c;
    --ink:#111111;
    --black:#0b0b0b;
    --paper:#ffffff;
    --backdrop-top:#e8e9ea;
    --backdrop-bottom:#262628;
    --photo-dark:#2a2318;
  }
  *{box-sizing:border-box;margin:0;padding:0}
  html,body{width:1146px;height:1200px;overflow:hidden}
  body{
    position:relative;
    font-family:'Lato',sans-serif;
    background:linear-gradient(to bottom,var(--backdrop-top) 0 938px,var(--backdrop-bottom) 938px);
  }
  .card{
    position:absolute;top:109px;width:437px;height:981px;
    background:var(--paper);overflow:hidden;
    box-shadow:0 2px 6px rgba(0,0,0,.25);
  }
  .card--front{left:128px}
  .card--back{left:581px}

  /* front */
  .hero{
    position:absolute;left:0;top:0;width:437px;height:506px;
    background:linear-gradient(160deg,#3a2f20 0%,var(--photo-dark) 55%,#1e1a12 100%);
  }
  .hero__image{
    position:absolute;left:15px;top:190px;width:410px;height:170px;
    background:radial-gradient(ellipse at 30% 55%,#5a1f1a 0%,transparent 45%),
               radial-gradient(ellipse at 70% 50%,#5a1f1a 0%,transparent 45%);
    opacity:.9;
  }
  .hero__title{
    position:absolute;left:0;right:0;top:28px;text-align:center;
    font-family:'Pinyon Script',cursive;color:var(--green);
    font-size:66px;line-height:76px;
  }
  .hero__band{
    position:absolute;left:0;top:369px;width:437px;height:36px;
    background:rgba(31,58,28,.85);
    color:#fff;font-weight:700;font-size:21px;line-height:36px;text-align:center;letter-spacing:.2px;
  }
  .hero__led{
    position:absolute;left:0;right:0;top:414px;text-align:center;
    color:#fff;font-size:15px;
  }
  .hero__name{
    position:absolute;left:0;right:0;top:436px;text-align:center;
    font-family:'Pinyon Script',cursive;color:var(--green);font-size:50px;line-height:60px;
  }
  .tree-art{
    position:absolute;left:272px;top:511px;width:165px;height:384px;
    background:radial-gradient(ellipse at 60% 30%,#c9dfc0 0%,#e2ede0 45%,rgba(255,255,255,0) 75%),
               linear-gradient(to bottom,rgba(255,255,255,0),#e4e4e4);
  }
  .topics{position:absolute;left:26px;top:545px}
  .topics__heading{color:var(--green-text);font-weight:700;font-size:30px;margin-bottom:6px}
  .topics__list{list-style:none}
  .topics__list li{font-size:17.5px;font-weight:700;color:var(--ink);line-height:25.5px;position:relative;padding-left:17px}
  .topics__list li::before{content:"";position:absolute;left:1px;top:10px;width:7px;height:7px;border-radius:50%;background:var(--green)}
  .info-bar{position:absolute;left:0;top:897px;width:437px;height:43px}
  .info-bar__label{position:absolute;top:0;line-height:43px;color:#fff;font-weight:700;font-size:18px}
  .info-bar__weeks{left:37px}
  .info-bar__cost{left:259px}
  .limit{position:absolute;left:0;right:0;top:945px;text-align:center;font-weight:700;font-size:17px;color:var(--ink)}

  /* back */
  .letter{
    position:absolute;left:0;top:0;width:437px;height:321px;background:var(--green);
    color:#fff;text-align:center;padding:31px 18px 0;font-size:14.4px;line-height:18.2px;
  }
  .letter p+p{margin-top:18px}
  .letter__sign{margin-top:10px;font-style:italic;font-weight:700;font-size:17px}
  .portrait{
    position:absolute;left:30px;top:332px;width:236px;height:285px;border-radius:10px;
    background:linear-gradient(to bottom,#b7a48a 0%,#9c8a74 45%,#8a7f75 100%);
  }
  .bio{
    position:absolute;left:278px;top:338px;width:150px;
    color:var(--green-text);font-style:italic;font-weight:700;font-size:16.5px;line-height:20.5px;
  }
  .bio-note{position:absolute;left:46px;top:628px;width:355px;font-weight:700;font-size:15px;line-height:19px;color:var(--ink)}
  .brand{
    position:absolute;left:0;right:0;top:755px;display:flex;align-items:center;justify-content:center;gap:12px;
    color:var(--green-text);font-weight:700;font-size:26px;
  }
  .brand__dot{width:22px;height:22px;border-radius:50%;background:var(--green)}
  .contact{position:absolute;left:0;right:0;top:872px;text-align:center;font-weight:700;font-size:19.5px;line-height:24px}
  .contact__lead{color:var(--green-text)}
  .contact__name{color:var(--ink)}
  .contact__lines{color:var(--green-text);font-size:19px}
  .foot-strip{position:absolute;left:0;top:963px;width:437px;height:18px}
</style>
</head>
<body>

<section class="card card--front">
  <div class="hero">
    <div class="hero__image" role="img" aria-label="Photo of two red felt hearts, one mended with bandages, on dark wood"></div>
    <h1 class="hero__title">Mending the<br>Weary Spirit</h1>
    <div class="hero__band">WOMEN'S TRAUMA &amp; LOSS GROUP</div>
    <p class="hero__led">Led by Licensed Professional Counselor,</p>
    <p class="hero__name">Lena Marsh Pruitt</p>
  </div>

  <div class="tree-art" role="img" aria-label="Soft faded tree illustration with green leaves"></div>

  <div class="topics">
    <h2 class="topics__heading">Topics Include:</h2>
    <ul class="topics__list">
      <li>What is Trauma?</li>
      <li>How Trauma Affects Us</li>
      <li>Creating a Feeling of Safety</li>
      <li>Managing Trauma Triggers</li>
      <li>Importance of Self Care</li>
      <li>Healthy vs. Unhealthy Coping</li>
      <li>Guilt, Shame, and Blame</li>
      <li>Victim vs. Victimized</li>
      <li>Grieving through Loss</li>
      <li>Anger and Forgiveness</li>
      <li>Imagining a Better Future</li>
    </ul>
  </div>

  <svg class="info-bar" viewBox="0 0 437 43" aria-hidden="true">
    <rect width="437" height="43" fill="var(--black)"/>
    <polygon points="238,0 437,0 437,43 212,43" fill="var(--green)"/>
  </svg>
  <span class="info-bar__label info-bar__weeks">10 Week Group</span>
  <span class="info-bar__label info-bar__cost">Cost $35 session</span>
  <p class="limit">Group size limited to10 participants</p>
</section>

<section class="card card--back">
  <div class="letter">
    <p>Life hurts and does not seem fair. &nbsp;So what do you do when you are faced with an event in your life that knocks you off your feet? &nbsp;It seems no one understands what you are feeling and no one knows just what to say. &nbsp;It is tempting to pull away and isolate or put up a mask and pretend everything is OK.</p>
    <p>It is my desire you know that you are not alone! &nbsp;There are others who understand the feelings you are going through and offer a safe place for encouraging support. &nbsp;I want to invite you to embark on a courageous journey of healing where you will not only learn how to "survive" after trauma and loss, but instead, learn that you can once again "thrive"!</p>
    <p class="letter__sign">- Lena Marsh Pruitt, LPC, LMFT</p>
  </div>

  <div class="portrait" role="img" aria-label="Photo of the counselor sitting on a blanket on a beach at sunset"></div>
  <p class="bio">Lena Marsh Pruitt is a Licensed Professional Counselor and Licensed Marriage and Family Therapist. She is the owner of Quiet Harbor Counseling Services located in Tulsa, OK.</p>

  <p class="bio-note">Lena is a trauma survivor herself and understands firsthand the unique challenges that can arise on the journey to healing.</p>

  <div class="brand"><span class="brand__dot"></span><span>Quiet Harbor Counseling</span></div>

  <div class="contact">
    <p class="contact__lead">For More Information, Contact:</p>
    <p class="contact__name">Lena Marsh Pruitt, LPC, LMFT</p>
    <p class="contact__lines">(555) 318-4926 | lena@calmwatersguide.example</p>
  </div>

  <svg class="foot-strip" viewBox="0 0 437 18" aria-hidden="true">
    <rect width="437" height="18" fill="var(--black)"/>
    <polygon points="236,0 437,0 437,18 227,18" fill="var(--green)"/>
  </svg>
</section>

</body>
</html>
```